Tessaryn Capital LLC

Need Professional Business cards for New Investment Fund

Target Market(s)

High Quality investors

Industry/Entity Type

Financial

Contact Information for Business Card

Phone Number +1 555 284 6190
Name Lukas Varenko
Title Fund Manager
email lv@FundCorvel.com
Website www.FundCorvel.com

Colors

Designer to choose colors to be used in the design.

Requirements
Must have
• Must have our Logo and all of the above. Must be made so lettering and loge can be raised

```html
<!DOCTYPE html>
<html lang="en">
<head>
<meta charset="utf-8">
<title>Tessaryn Capital LLC – Business Card</title>
<link rel="stylesheet" href="https://fonts.googleapis.com/css2?family=Lato:wght@400;700;900&display=swap">
<style>
  :root {
    --stage: #2b2b2d;
    --card-dark: #1c1d1f;
    --pattern-tone: #26282a;
    --accent-green: #1fe500;
    --ink: #111213;
  }
  * { margin: 0; padding: 0; box-sizing: border-box; }
  html, body { width: 1200px; height: 1108px; overflow: hidden; }
  body {
    background: var(--stage);
    font-family: "Lato", sans-serif;
    display: flex;
    align-items: center;
    justify-content: center;
    gap: 80px;
  }
  .card {
    position: relative;
    width: 440px;
    height: 740px;
    border-radius: 26px;
    overflow: hidden;
    background: var(--card-dark);
  }
  .card-front .green-panel {
    position: absolute;
    inset: 0;
    width: 100%;
    height: 100%;
  }
  .brand-mark {
    position: absolute;
    left: 0; right: 0;
    top: 190px;
    display: flex;
    align-items: center;
    justify-content: center;
    gap: 12px;
  }
  .brand-dot {
    width: 26px; height: 26px;
    border-radius: 50%;
    background: var(--accent-green);
  }
  .brand-name {
    font-weight: 700;
    font-size: 44px;
    color: var(--accent-green);
    letter-spacing: 1px;
  }
  .contact-block {
    position: absolute;
    left: 0; right: 0;
    top: 448px;
    text-align: center;
    color: var(--ink);
  }
  .person-name {
    font-weight: 900;
    font-size: 27px;
    letter-spacing: 0.5px;
    text-transform: uppercase;
  }
  .person-title {
    font-size: 19px;
    margin-top: 2px;
  }
  .icon-row {
    display: flex;
    align-items: center;
    justify-content: center;
    gap: 6px;
    margin: 16px 0 14px;
  }
  .icon-row .rule {
    width: 82px;
    height: 1px;
    background: var(--ink);
    margin: 0 8px;
  }
  .icon-row svg { width: 28px; height: 28px; }
  .contact-line {
    font-size: 21px;
    line-height: 1.3;
  }
  .card-back .logo-pattern {
    position: absolute;
    inset: 0;
    background: linear-gradient(160deg, var(--pattern-tone), var(--card-dark));
  }
  .card-back .back-mark {
    position: absolute;
    right: 48px;
    bottom: 170px;
    display: flex;
    align-items: center;
    gap: 8px;
  }
  .card-back .brand-dot { width: 14px; height: 14px; }
  .card-back .brand-name { font-size: 24px; }
</style>
</head>
<body>
  <article class="card card-front">
    <svg class="green-panel" viewBox="0 0 440 740" aria-hidden="true">
      <polygon points="0,366 32,338 108,338 108,398 440,398 440,740 0,740" fill="var(--accent-green)"/>
    </svg>
    <div class="brand-mark">
      <span class="brand-dot"></span>
      <span class="brand-name">Tessaryn</span>
    </div>
    <div class="contact-block">
      <p class="person-name">Lukas Varenko</p>
      <p class="person-title">Fund Manager</p>
      <div class="icon-row">
        <span class="rule"></span>
        <svg viewBox="0 0 28 28" aria-label="phone">
          <circle cx="14" cy="14" r="12.5" fill="none" stroke="var(--ink)" stroke-width="2"/>
          <circle cx="14" cy="14" r="9.5" fill="var(--ink)"/>
          <path d="M10 9.5c.8-.8 1.7-.6 2.2.3l.7 1.3c.3.6.1 1.1-.4 1.5l-.5.4c.5 1.2 1.5 2.2 2.7 2.7l.4-.5c.4-.5 1-.7 1.5-.4l1.3.7c.9.5 1.1 1.4.3 2.2-1.5 1.5-4 .6-6-1.4s-2.9-4.5-2.2-7z" fill="var(--accent-green)"/>
        </svg>
        <svg viewBox="0 0 28 28" aria-label="email">
          <circle cx="14" cy="14" r="12.5" fill="none" stroke="var(--ink)" stroke-width="2"/>
          <circle cx="14" cy="14" r="9.5" fill="var(--ink)"/>
          <rect x="8.5" y="10" width="11" height="8" fill="none" stroke="var(--accent-green)" stroke-width="1.4"/>
          <path d="M8.5 10l5.5 4.5 5.5-4.5" fill="none" stroke="var(--accent-green)" stroke-width="1.4"/>
        </svg>
        <svg viewBox="0 0 28 28" aria-label="website">
          <circle cx="14" cy="14" r="12.5" fill="none" stroke="var(--ink)" stroke-width="2"/>
          <circle cx="14" cy="14" r="9.5" fill="var(--ink)"/>
          <circle cx="14" cy="14" r="5.5" fill="none" stroke="var(--accent-green)" stroke-width="1.3"/>
          <ellipse cx="14" cy="14" rx="2.3" ry="5.5" fill="none" stroke="var(--accent-green)" stroke-width="1.1"/>
          <path d="M8.5 14h11" stroke="var(--accent-green)" stroke-width="1.1"/>
        </svg>
        <span class="rule"></span>
      </div>
      <p class="contact-line">+1 555 284 6190</p>
      <p class="contact-line">lv@FundCorvel.com</p>
      <p class="contact-line">www.FundCorvel.com</p>
    </div>
  </article>

  <article class="card card-back">
    <div class="logo-pattern" role="img" aria-label="Faint repeating brand pattern in dark grey tones"></div>
    <div class="back-mark">
      <span class="brand-dot"></span>
      <span class="brand-name">Tessaryn</span>
    </div>
  </article>
</body>
</html>
```